Help Give House Painter “Fresh” Website Makeover!

A residential and commercial painting company based in Albuquerque, NM, USA needs a fresh, new, fun, and playful--yet, simple, elegant and professional--website made.

Here is a link to their existing site:

http://corvelcoatings.example/

We want to keep a similar site structure., So the navigation layout will stay the same. However, the video is too small, is too far over in the sidebar, and the overall design is amateur at best. We want something bright, colorful and bold!

We will need a space for the Video above the fold, and there needs to be space in the design for Testimonials, Specials and Images. It’s also very important to have the Pellham Roster awards that you see on his current website.

Please also include somewhere in the Design icons for YouTube, Facebook, Google+ and LinkedIn.

Here are some examples to look at to get your creative juices flowing!

http://brightloombrush.example/

http://www.tkvr.example/

http://www.marblow-tennick.example/

http://www.quarrypages.example/painting-company-niche-website/

http://www.brisklayoutdepot.example/website-templates/painting-company-website-template-53817.html

We have accounts at both lumavault.example and pixaroo.example. If you use placeholder images from there, that's fine. We can buy the images when and if your design is selected.

Target Market(s)

The audience is the average middle class homeowner to higher upper class. This should appeal to families, couples, and singles who own a home.

Industry/Entity Type

Residential

Font styles to use
Sans Serif

Requirements
Must have
• - - Lots of color! It's a site about painting homes. People like a variety of colors. Bring out your inner artist, and get bold with your colors!

- - A video place holder. As you can see, there is a video on the existing site, but it's small and hidden. Make it big and put it top left, or in the center.

- -Detailed and organized PSD structure. We're going to turn your design into a website, and to make that work soothly, we ask that you organize you PSD well: name your layers, keep things separated, group and ungroup as necessary, etc.

- A sidebar that goes down the right side of an interior page. We need a homepage, and also one [1] interior page template. We don't need you to make a design for each page. Just the homepage, followed by a simple interior page design that requires only the header/navigation, and a sidebar down the right side.
Should not have
• - Coding. This is a design project only.

```html
<!DOCTYPE html>
<html lang="en">
<head>
<meta charset="utf-8">
<title>Corvel's Painting – Residential &amp; Commercial Painting</title>
<link href="https://fonts.googleapis.com/css2?family=Lato:wght@400;700;900&family=Oswald:wght@500;600&display=swap" rel="stylesheet">
<style>
:root{
  --red:#e41b23;
  --blue:#0c4da2;
  --navy:#17264a;
  --navy-deep:#0f1a35;
  --orange:#f7830f;
  --cyan:#29a3e0;
  --green:#5aae13;
  --ink:#333;
  --muted:#555;
  --white:#fff;
}
*{margin:0;padding:0;box-sizing:border-box}
html,body{width:1200px;height:2365px;overflow:hidden}
body{position:relative;font-family:"Lato",sans-serif;color:var(--ink);background:var(--white)}
.abs{position:absolute}

/* header */
.site-header{left:0;top:0;width:1200px;height:140px;background:var(--white)}
.brand{left:132px;top:36px;height:70px;display:flex;align-items:center;gap:16px}
.brand-dot{width:66px;height:66px;border-radius:50%;background:var(--blue)}
.brand-name{font-weight:900;font-size:38px;color:var(--blue);line-height:1;letter-spacing:.5px}
.award-badge{left:765px;top:22px;width:66px;height:90px;border-radius:8px 8px 33px 33px;background:linear-gradient(#e8c14a,#b48a1c)}
.phone{left:906px;top:26px;display:flex;align-items:center;gap:10px;font-weight:700;font-size:23px;color:var(--red)}
.estimate-btn{left:857px;top:72px;width:206px;height:40px;background:var(--blue);border-radius:4px;color:var(--white);font-weight:900;font-size:20px;text-align:center;line-height:40px;letter-spacing:.5px}

/* navigation */
.main-nav{left:0;top:140px;width:1200px;height:48px;background:var(--red)}
.main-nav ul{list-style:none;display:flex;position:absolute;left:132px;top:0;height:48px}
.main-nav li{color:var(--white);font-family:"Oswald",sans-serif;font-weight:500;font-size:16px;line-height:48px;padding:0 14px;border-right:1px solid rgba(255,255,255,.35)}
.main-nav li.active{background:var(--blue);padding:0 20px}

/* hero */
.hero{left:0;top:188px;width:1200px;height:570px;background:linear-gradient(100deg,#e7e5e0 0%,#dedbd4 55%,#cfcac0 100%)}
.hero-photo{right:0;top:0;width:520px;height:570px;background:linear-gradient(180deg,rgba(200,195,185,0),rgba(175,170,160,.45))}
.hero-title{left:130px;top:212px;font-family:"Oswald",sans-serif;font-weight:600;font-size:54px;line-height:70px;color:#2b2b2b}
.hero-title .b{color:var(--blue)} .hero-title .r{color:var(--red)}
.slider-arrow{top:262px;width:34px;height:34px}

/* welcome */
.welcome{left:0;top:758px;width:1200px;height:370px;background:linear-gradient(#e6f0fa,#c9dff2)}
.video-box{left:132px;top:47px;width:396px;height:265px;background:var(--white);padding:8px;box-shadow:0 3px 8px rgba(0,0,0,.2)}
.video-frame{width:380px;height:217px;background:linear-gradient(120deg,#c7d3b8,#b9a58f)}
.video-play{left:174px;top:92px;width:46px;height:34px;background:var(--red);border-radius:8px}
.video-bar{width:380px;height:32px;background:#1e1e1e;position:relative}
.video-bar .track{position:absolute;left:70px;top:14px;width:250px;height:5px;background:#555}
.video-bar .fill{position:absolute;left:70px;top:14px;width:100px;height:5px;background:var(--cyan)}
.welcome-box{left:535px;top:47px;width:533px;height:265px;background:var(--white);padding:14px 18px;box-shadow:0 3px 8px rgba(0,0,0,.2)}
.welcome-box h2{font-size:22px;font-weight:700;color:var(--blue)}
.welcome-box h2 span{color:var(--red)}
.welcome-box p{font-size:13.5px;line-height:20px;color:var(--muted);margin-top:10px;text-align:justify;letter-spacing:.3px}
.share{display:flex;gap:10px;margin-top:10px}
.share i{width:28px;height:28px;display:block;border-radius:3px}

/* feature cards */
.features{left:0;top:1128px;width:1200px;height:547px;background:radial-gradient(ellipse at 50% 30%,#26385f,var(--navy-deep))}
.card{top:60px;width:283px;height:400px;color:var(--white);text-align:center;padding:24px 16px}
.card.orange{left:132px;background:var(--orange)}
.card.cyan{left:462px;background:var(--cyan)}
.card.green{left:785px;background:var(--green)}
.card h3{font-size:20px;font-weight:700;line-height:26px}
.card .card-img{width:245px;height:152px;margin:14px auto 0;border:6px solid var(--white)}
.card p{font-size:13px;line-height:20px;color:#111;margin-top:16px;height:60px;overflow:hidden}
.card .more{font-size:13px;font-weight:700;color:#111;margin-top:18px}

/* review */
.review{left:0;top:1675px;width:1200px;height:330px;background:linear-gradient(#e3eef9,#bcd6ef)}
.review h2{position:absolute;left:0;top:36px;width:1200px;text-align:center;font-size:30px;font-weight:700;color:var(--blue)}
.review h2 span{color:var(--red)}
.review .sub{position:absolute;left:0;top:82px;width:1200px;text-align:center;font-size:15px;color:var(--muted)}
.stars{left:575px;top:104px}
.quote-box{left:132px;top:135px;width:800px;height:100px;background:var(--white);padding:14px 22px;border-radius:4px;box-shadow:0 2px 6px rgba(0,0,0,.15)}
.quote-box p{font-size:13px;line-height:22px;font-style:italic;color:var(--muted)}
.avatar{left:930px;top:130px;width:120px;height:120px;border-radius:50%;border:5px solid var(--white);background:linear-gradient(#c9d7e6,#8aa4c0);box-shadow:0 2px 6px rgba(0,0,0,.2)}
.reviewer{left:780px;top:253px;font-size:13px;font-weight:700;font-style:italic;color:var(--ink)}

/* footer */
.site-footer{left:0;top:2005px;width:1200px;height:295px;background:var(--navy)}
.site-footer h4{font-size:19px;font-weight:700;color:var(--white)}
.newsletter{left:132px;top:30px;width:220px}
.newsletter p{font-size:13px;line-height:19px;color:#d8deea;margin-top:16px}
.newsletter .field{width:206px;height:30px;background:var(--white);margin-top:10px;font-size:12px;color:#888;padding:8px 10px}
.newsletter .btn{width:88px;height:30px;background:var(--red);color:var(--white);font-size:13px;line-height:30px;text-align:center;margin-top:14px;border-radius:2px}
.quick-links{left:400px;top:0;width:390px;height:295px;background:#1d2d55;padding:30px 34px}
.quick-links ul{list-style:none;display:grid;grid-template-columns:160px 160px;row-gap:11px;margin-top:20px}
.quick-links li{font-size:13.5px;line-height:17px;color:#e4e9f3}
.quick-links li::before{content:"›";margin-right:10px;color:#aab}
.contact-btn{left:28px;top:220px;width:310px;height:50px;background:var(--blue);border-radius:4px;color:var(--white);text-align:center;line-height:50px;font-size:17px;font-weight:700}
.contact-btn b{font-size:24px;margin-left:6px}
.location{left:835px;top:30px}
.map{margin-top:18px;width:235px;height:180px;background:linear-gradient(135deg,#e4ecd9,#cfdcc2);border:3px solid var(--white);position:relative}
.map-card{position:absolute;left:68px;top:38px;width:104px;padding:6px 8px;background:var(--white);font-size:12px;line-height:16px;color:var(--ink);border-radius:3px;box-shadow:0 1px 4px rgba(0,0,0,.3)}
.bottom-bar{left:0;top:2300px;width:1200px;height:65px;background:var(--navy-deep)}
.social{left:132px;top:20px;display:flex;gap:10px}
.social i{display:block;width:26px;height:26px;border-radius:50%;background:var(--cyan)}
.social i:first-child{background:#3b5b99}
.copyright{left:0;top:24px;width:1200px;text-align:center;font-size:13px;color:#cfd6e4;letter-spacing:.5px}
.corner-dot{left:1024px;top:14px;width:36px;height:36px;border-radius:50%;background:var(--cyan)}
</style>
</head>
<body>

<header class="site-header abs">
  <div class="brand abs">
    <div class="brand-dot"></div>
    <div class="brand-name">CORVEL'S PAINTING</div>
  </div>
  <div class="award-badge abs" role="img" aria-label="Pellham Roster service award badge"></div>
  <div class="phone abs">
    <svg width="24" height="24" viewBox="0 0 24 24"><circle cx="12" cy="12" r="11" fill="none" stroke="#111" stroke-width="2"/><path d="M8 6l2 0 1 3-1.5 1a7 7 0 0 0 4 4l1-1.5 3 1v2c-6 1-11-4-10-10z" fill="#111"/></svg>
    123 456 7890
  </div>
  <div class="estimate-btn abs">FREE ESTIMATES</div>
</header>

<nav class="main-nav abs">
  <ul>
    <li class="active">HOME</li><li>ABOUT US</li><li>RESIDENTIAL PAINTING</li><li>COMMERCIAL PAINTING</li><li>FAQ</li><li>SPECIALS</li><li>BLOG</li><li>TESTIMONIALS</li><li>CONTACT US</li>
  </ul>
</nav>

<section class="hero abs">
  <div class="hero-photo abs" role="img" aria-label="Painter on a ladder rolling paint onto a wall"></div>
  <h1 class="hero-title abs"><span class="b">Residential &amp;</span> <span class="r">Commercial</span><br>Painting Company</h1>
  <svg class="slider-arrow abs" style="left:8px" viewBox="0 0 34 34"><rect width="34" height="34" fill="#3a3a3a"/><path d="M20 10l-7 7 7 7" stroke="#fff" stroke-width="3" fill="none"/></svg>
  <svg class="slider-arrow abs" style="left:1158px" viewBox="0 0 34 34"><rect width="34" height="34" fill="#3a3a3a"/><path d="M14 10l7 7-7 7" stroke="#fff" stroke-width="3" fill="none"/></svg>
</section>

<section class="welcome abs">
  <div class="video-box abs">
    <div class="video-frame" role="img" aria-label="Video still of a painter at work on a ladder"></div>
    <div class="video-play abs"><svg width="46" height="34" viewBox="0 0 46 34"><path d="M18 10l12 7-12 7z" fill="#fff"/></svg></div>
    <div class="video-bar">
      <svg class="abs" style="left:10px;top:9px" width="40" height="14" viewBox="0 0 40 14"><path d="M0 0l10 7-10 7z" fill="#ddd"/><path d="M24 4h4l5-4v14l-5-4h-4z" fill="#ddd"/></svg>
      <span class="track"></span><span class="fill"></span>
    </div>
  </div>
  <div class="welcome-box abs">
    <h2>Welcome To CORVEL'S <span>PAINTING</span></h2>
    <p>Corvel's Painting does jobs as small as a bathroom up to large commercial projects right here in Albuquerque and Rio Rancho. Extensive as an entire apartment exterior, to a kitchen and all home interior, no job is too big or too small for Corvel's Painting of Albuquerque. Corvel's Painting is staffed with the best painters for the highest quality paint jobs. Corvel's Painting is not a community's average house painter staffing company, but this painting company is staffed with professional painters that pride themselves on successfully completing every job.</p>
    <div class="share"><i style="background:#3b5b99"></i><i style="background:var(--cyan)"></i></div>
  </div>
</section>

<section class="features abs">
  <article class="card orange abs">
    <h3>Our Painting<br>In Albuquerque</h3>
    <div class="card-img" style="background:linear-gradient(135deg,#f2c9a6,#a7d07a)" role="img" aria-label="Couple painting a wall green"></div>
    <p>Corvel's Painting does jobs as small as a bathroom up to large commercial projects right here in Albuquerque.</p>
    <div class="more">Read More »</div>
  </article>
  <article class="card cyan abs">
    <h3>Albuquerque<br>Painter Videos</h3>
    <div class="card-img" style="background:linear-gradient(135deg,#f0a531,#d9702a)" role="img" aria-label="Paint roller on an orange wall"></div>
    <p>We have shot a ton of videos with Corvel answering all of your most frequently asked questions. We want</p>
    <div class="more">Read More »</div>
  </article>
  <article class="card green abs">
    <h3>Happy Albuquerque<br>Painting Customers</h3>
    <div class="card-img" style="background:linear-gradient(135deg,#eaf3fb,#8cc0e6)" role="img" aria-label="Woman painting a wall light blue"></div>
    <p>100% Customer Satisfaction is our Ultimate Goal. We are proud to have served so many clients in an around</p>
    <div class="more">Read More »</div>
  </article>
</section>

<section class="review abs">
  <h2>Our Customer <span>Review</span></h2>
  <div class="sub">Lorem ipsum dolor sit amet, consectetur Donec a consequat mag Aenean eu velit Aenean sollicitudin</div>
  <svg class="stars abs" width="50" height="14" viewBox="0 0 50 14"><g fill="#f0b400"><path d="M7 0l2 5h5l-4 3 2 5-5-3-5 3 2-5-4-3h5z"/><path transform="translate(18 0)" d="M7 0l2 5h5l-4 3 2 5-5-3-5 3 2-5-4-3h5z"/><path transform="translate(36 0)" d="M7 0l2 5h5l-4 3 2 5-5-3-5 3 2-5-4-3h5z"/></g></svg>
  <div class="quote-box abs">
    <p>“ Lorem sum dolor sit amet, consectetuer adipiscing elit, sed diam nonummy nibh euismod tincidunt ut laoreet re agn aliqam erat volutpat wisi enim ad minim veniam, quis nostrud exerci tation ullamcorper suscipit lobortis nisl ut aliquip modo conseuatis autem vel eum iriure dolor in hendrerit in vulputate velit esse molestie consequat, vel illum dolore eu.</p>
  </div>
  <div class="avatar abs" role="img" aria-label="Customer portrait"></div>
  <div class="reviewer abs">Ravel, Fenlock Studio , USA</div>
</section>

<footer class="site-footer abs">
  <div class="newsletter abs">
    <h4>Newsletter Signup</h4>
    <p>Lorem ipsum dolor sit amet, consectetu er adipiscing elit, sed</p>
    <div class="field">Name</div>
    <div class="field">Email</div>
    <div class="btn">Subscribe</div>
  </div>
  <div class="quick-links abs">
    <h4>Quick Links</h4>
    <ul>
      <li>Home</li><li>Specials</li><li>About Us</li><li>Blog</li><li>Residential Painting</li><li>Testimonials</li><li>Commercial Painting</li><li>Contact Us</li><li>Faq</li>
    </ul>
    <div class="contact-btn abs">CONTACT US <b>123-456-7890</b></div>
  </div>
  <div class="location abs">
    <h4>View Location</h4>
    <div class="map" role="img" aria-label="Street map showing the office location">
      <div class="map-card">67 Lorem ipsum Street WA 6065, adipsimg amet</div>
      <svg class="abs" style="left:40px;top:70px" width="16" height="22" viewBox="0 0 16 22"><path d="M8 0a8 8 0 0 1 8 8c0 6-8 14-8 14S0 14 0 8a8 8 0 0 1 8-8z" fill="#e41b23"/><circle cx="8" cy="8" r="3" fill="#fff"/></svg>
    </div>
  </div>
</footer>

<div class="bottom-bar abs">
  <div class="social abs"><i></i><i></i><i style="background:#1a84bc"></i></div>
  <div class="copyright abs">© 2015 CORVEL'S PAINTING. ALL RIGHT RESERVED.</div>
  <div class="corner-dot abs"></div>
</div>

</body>
</html>
```